Business card design needed

I run a Beautician studio (for 7 years now)
I offer
- Velmo Body Sugaring
- Ruby Glaze
- Nails
- Facials
- Manicure
- Foot Treatment
It might not be necessary to list all those treatments?
Maybe the link to the Website is sufficient?
I leave that up to you ...
(more info on www.FernAndDewByLenka.com.au)
Velmo BodySugaring is our biggest success, It replaces waxing.
I would like to incorporate the logo into the Business Card.
We had many complaints regarding our old Business Cards as the Phone Number was to small.
On the backside, we would like a "your next Appointment" section.
Looking forward to you Design, cheers ... Lenka
Industry/Entity Type
Business
Contact Information for Business Card
Fern by Dew by Lenka
14 Korrin Sqr 3942 Dunmore
www.FernAndDewByLenka.com.au
03 9481 2267

```html
<!DOCTYPE html>
<html lang="en">
<head>
<meta charset="utf-8">
<title>Fern by Dew by Lenka – Business Cards</title>
<link href="https://fonts.googleapis.com/css2?family=Open+Sans:wght@400;600;700&family=Tinos:wght@700&family=Cinzel:wght@500&display=swap" rel="stylesheet">
<style>
  :root {
    --backdrop: #1c1c1c;
    --card: #ffffff;
    --ink: #222222;
    --ink-soft: #555555;
    --grey: #4a4a4a;
    --green: #1e8a3a;
    --green-dark: #1d5a2c;
    --orange: #f08a1c;
    --orange-deep: #e2571b;
    --gold: #f7b827;
    --rule: #9a9a9a;
    --box: #6f6f6f;
  }
  * { box-sizing: border-box; margin: 0; padding: 0; }
  html, body { width: 1200px; height: 728px; overflow: hidden; }
  body {
    background: var(--backdrop);
    font-family: "Open Sans", Arial, sans-serif;
    color: var(--ink);
    position: relative;
  }
  .card {
    position: absolute;
    width: 542px;
    height: 308px;
    background: var(--card);
    overflow: hidden;
  }
  .card--front { left: 41px; top: 37px; }
  .card--appointment { left: 616px; top: 37px; }
  .card--back { left: 41px; top: 380px; width: 544px; }
  .card--appointment-plain { left: 624px; top: 384px; width: 541px; }
  .abs { position: absolute; }

  /* Front card */
  .studio-name {
    left: 48px; top: 32px;
    font-family: "Tinos", "Times New Roman", serif;
    font-weight: 700;
    font-size: 35px;
    letter-spacing: 0.5px;
    background: linear-gradient(180deg, var(--gold) 0%, var(--orange) 55%, var(--orange-deep) 100%);
    -webkit-background-clip: text;
    background-clip: text;
    color: transparent;
    white-space: nowrap;
  }
  .treatments-title {
    left: 45px; top: 104px;
    color: var(--green);
    font-weight: 700;
    font-size: 16.5px;
    letter-spacing: 0.6px;
  }
  .treatments {
    left: 45px; top: 128px;
    list-style: none;
    font-size: 14.5px;
    line-height: 22px;
    display: grid;
    grid-template-columns: 178px auto;
    color: var(--ink);
  }
  .contact {
    left: 36px;
    display: flex;
    align-items: center;
    gap: 8px;
    white-space: nowrap;
  }
  .contact--phone { top: 192px; font-size: 16.5px; }
  .contact--web { top: 222px; font-size: 14px; }
  .contact svg { flex: none; }
  .address { left: 36px; top: 258px; font-size: 14px; color: var(--ink-soft); }

  /* Brand stand-in */
  .brand {
    display: flex;
    flex-direction: column;
    align-items: center;
    gap: 10px;
  }
  .brand__dot {
    border-radius: 50%;
    background: linear-gradient(180deg, var(--gold), var(--orange-deep));
  }
  .brand__name {
    font-family: "Open Sans", Arial, sans-serif;
    font-weight: 400;
    color: var(--ink);
    text-transform: uppercase;
    text-align: center;
    line-height: 1.3;
  }
  .brand--front { left: 360px; top: 168px; width: 160px; }
  .brand--front .brand__dot { width: 64px; height: 64px; }
  .brand--front .brand__name { font-size: 15px; letter-spacing: 3px; }

  .brand--corner { left: 372px; top: 16px; width: 120px; gap: 6px; }
  .brand--corner .brand__dot { width: 42px; height: 42px; }
  .brand--corner .brand__name { font-size: 10px; letter-spacing: 2px; }

  .brand--back { left: 0; top: 22px; width: 100%; gap: 12px; }
  .brand--back .brand__dot { width: 104px; height: 104px; }
  .brand--back .brand__name { font-size: 24px; letter-spacing: 5px; }

  .watermark {
    left: 0; top: 150px; width: 100%;
    text-align: center;
    font-size: 40px;
    letter-spacing: 10px;
    text-transform: uppercase;
    color: var(--ink);
    opacity: 0.03;
    line-height: 1.3;
  }

  /* Back card */
  .web-line {
    left: 0; top: 206px; width: 100%;
    text-align: center;
    font-size: 14.5px;
    letter-spacing: 2.2px;
  }
  .hours-title {
    left: 0; top: 238px; width: 100%;
    text-align: center;
    font-size: 20px;
    font-weight: 600;
    letter-spacing: 1.5px;
    color: var(--grey);
  }
  .hours {
    left: 0; top: 276px; width: 100%;
    text-align: center;
    font-size: 15.5px;
    font-weight: 600;
    color: var(--grey);
  }
  .hours__sep { color: var(--rule); font-weight: 400; margin: 0 6px; }

  /* Appointment card */
  .appt-title {
    left: 34px; top: 54px;
    font-family: "Cinzel", "Times New Roman", serif;
    font-weight: 500;
    font-size: 18px;
    color: var(--green-dark);
    letter-spacing: 0.5px;
  }
  .field {
    left: 34px;
    display: flex;
    align-items: flex-end;
    font-size: 15px;
    color: var(--ink);
    white-space: nowrap;
  }
  .field__line { border-bottom: 1px solid var(--rule); height: 1px; margin: 0 6px 6px; }
  .field__line--dotted { border-bottom: 1px dotted var(--rule); }
  .field--name { top: 90px; }
  .field--date { top: 128px; }
  .field--next { top: 166px; align-items: center; }
  .slot { width: 96px; height: 21px; border: 1px solid var(--box); }
  .days {
    left: 30px; top: 204px;
    display: flex;
    align-items: center;
    gap: 6px;
    font-size: 15px;
    font-weight: 600;
    color: var(--grey);
  }
  .day-box { width: 35px; height: 21px; border: 1px solid var(--box); margin-right: 6px; }
  .notice {
    left: 30px; top: 250px; width: 480px;
    font-size: 13px;
    line-height: 19px;
    color: var(--ink);
  }
</style>
</head>
<body>

  <!-- Front -->
  <section class="card card--front">
    <h1 class="abs studio-name">FERN BY DEW BY LENKA</h1>
    <h2 class="abs treatments-title">Treatments offer</h2>
    <ul class="abs treatments">
      <li>• Velmo Body Sugaring</li>
      <li>• Facials • Manicure</li>
      <li>• Ruby Glaze • Nails</li>
      <li>• Foot Treatment</li>
    </ul>
    <div class="abs contact contact--phone">
      <svg width="14" height="14" viewBox="0 0 24 24" aria-hidden="true"><path fill="var(--green)" d="M6.6 10.8a15 15 0 0 0 6.6 6.6l2.2-2.2a1 1 0 0 1 1-.25 11.4 11.4 0 0 0 3.6.57 1 1 0 0 1 1 1V20a1 1 0 0 1-1 1A17 17 0 0 1 3 4a1 1 0 0 1 1-1h3.5a1 1 0 0 1 1 1c0 1.25.2 2.45.57 3.57a1 1 0 0 1-.25 1z"/></svg>
      <span>03 9481 2267</span>
    </div>
    <div class="abs contact contact--web">
      <svg width="14" height="14" viewBox="0 0 24 24" aria-hidden="true"><circle cx="12" cy="12" r="10" fill="var(--green)"/><path d="M2 12h20M12 2c3 3 3 17 0 20M12 2c-3 3-3 17 0 20" stroke="#fff" stroke-width="1.4" fill="none"/></svg>
      <span>www.FernAndDewByLenka.com.au</span>
    </div>
    <p class="abs address">14 Korrin Sqr 3942 Dunmore</p>
    <div class="abs brand brand--front">
      <span class="brand__dot"></span>
      <span class="brand__name">Velmo<br>Body Sugaring</span>
    </div>
  </section>

  <!-- Appointment with brand -->
  <section class="card card--appointment">
    <h2 class="abs appt-title">YOUR APPOINTMENT</h2>
    <div class="abs brand brand--corner">
      <span class="brand__dot"></span>
      <span class="brand__name">Velmo Body Sugaring</span>
    </div>
    <div class="abs field field--name">Name :<span class="field__line field__line--dotted" style="width:300px"></span></div>
    <div class="abs field field--date">Date :<span class="field__line" style="width:96px;margin-left:16px"></span>Time :<span class="field__line" style="width:90px"></span>am / pm</div>
    <div class="abs field field--next">Next Appointment<span class="slot" style="margin-left:10px"></span><span class="slot" style="margin-left:31px"></span></div>
    <div class="abs days">
      MON <span class="day-box"></span> TUE <span class="day-box"></span> WED <span class="day-box"></span> THU <span class="day-box"></span> FRI <span class="day-box"></span> SAT <span class="day-box"></span>
    </div>
    <p class="abs notice">It would be appreciated if 24 hours notice could be given if you are unable to attend an appointment</p>
  </section>

  <!-- Back -->
  <section class="card card--back">
    <div class="abs brand brand--back">
      <span class="brand__dot"></span>
      <span class="brand__name">Velmo Body Sugaring</span>
    </div>
    <p class="abs web-line">www.FernAndDewByLenka.com.au</p>
    <h2 class="abs hours-title">Hours of Operation</h2>
    <p class="abs hours">Mon - Fri: 8.00am - 6.30pm<span class="hours__sep">|</span>Saturday: 8.30am - 1.00pm</p>
  </section>

  <!-- Appointment plain -->
  <section class="card card--appointment-plain">
    <p class="abs watermark" aria-hidden="true">Velmo<br>Body Sugaring</p>
    <h2 class="abs appt-title">YOUR APPOINTMENT</h2>
    <div class="abs field field--name">Name :<span class="field__line field__line--dotted" style="width:300px"></span></div>
    <div class="abs field field--date">Date :<span class="field__line" style="width:96px;margin-left:16px"></span>Time :<span class="field__line" style="width:90px"></span>am / pm</div>
    <div class="abs field field--next">Next Appointment<span class="slot" style="margin-left:10px"></span><span class="slot" style="margin-left:31px"></span></div>
    <div class="abs days">
      MON <span class="day-box"></span> TUE <span class="day-box"></span> WED <span class="day-box"></span> THU <span class="day-box"></span> FRI <span class="day-box"></span> SAT <span class="day-box"></span>
    </div>
    <p class="abs notice">It would be appreciated if 24 hours notice could be given if you are unable to attend an appointment</p>
  </section>

</body>
</html>
```